Creative, fresh business card design for Ripplecraft Facades

We need a fresh, creative business card design for Ripplecraft Facades. We are the manufacturer of Ripplecraft Facades in Australia. Wall panels are 2400 x 1200mm panels made from MDF and feature 3D patterns on the face of the panel. The colours to be used are green, silver/grey and white RGB
Red 187
Green 207
Blue 65.

An idea is to possibly use a watermark of one of our designs as a background (like on the "Grids" design on the left hand side of page 2 of our brochure).

Target Market(s)

Interior designers, architects, builders and home renovators

Industry/Entity Type

Business

Contact Information for Business Card

Details to go on the card are:
Our logo (attached),
Slogan: "Decorative panels for interiors and exteriors",
Contact name,
Position,
Mobile phone number,
Business address,
Business phone,
Business fax,
Website and
Email address.

I have attached a few images of our panels and our brochure for reference.

The colours of the business card should feature our logo colours which are: RGB
Red 187
Green 207
Blue 65

Requirements
Must have
• Very modern fonts and design. Some of the designs shown especially the "Prisms" design which is a popular design.
Nice to have
• Creative but simple design. Very contemporary.
Should not have
• Anything ornate or old fashioned.

```html
<!DOCTYPE html>
<html lang="en">
<head>
<meta charset="utf-8">
<title>Ripplecraft Facades – Business Card</title>
<link rel="stylesheet" href="https://fonts.googleapis.com/css2?family=Poppins:wght@600;800&family=Lato:wght@400;700&display=swap">
<style>
  :root {
    --brand-green: #bbcf41;
    --green-mid: #8a9c24;
    --green-deep: #5e6d14;
    --silver: #d4d8dc;
    --text-white: #ffffff;
  }
  html, body {
    margin: 0;
    padding: 0;
    width: 1200px;
    height: 667px;
    overflow: hidden;
    background: var(--green-mid);
  }
  .card {
    position: relative;
    width: 1200px;
    height: 667px;
    overflow: hidden;
  }
  .panel-texture {
    position: absolute;
    inset: 0;
    background: linear-gradient(178deg, var(--brand-green) 0%, var(--green-mid) 45%, var(--green-deep) 100%);
  }
  .brand-name {
    position: absolute;
    left: 0;
    right: 0;
    top: 120px;
    margin: 0;
    text-align: center;
    font-family: "Poppins", sans-serif;
    font-weight: 800;
    font-size: 70px;
    line-height: 1;
    color: var(--text-white);
  }
  .slogan {
    position: absolute;
    left: 0;
    right: 0;
    top: 222px;
    margin: 0;
    text-align: center;
    font-family: "Poppins", sans-serif;
    font-weight: 600;
    font-size: 27px;
    line-height: 1.2;
    color: var(--text-white);
  }
  .divider {
    position: absolute;
    left: 450px;
    top: 290px;
    width: 300px;
    height: 2px;
    background: var(--silver);
  }
  .contact {
    position: absolute;
    left: 190px;
    top: 320px;
    width: 820px;
    display: grid;
    grid-template-columns: 1fr 1fr;
    column-gap: 60px;
    font-family: "Lato", sans-serif;
    font-size: 19px;
    line-height: 34px;
    color: var(--text-white);
  }
  .contact p { margin: 0; }
  .contact-person { text-align: right; }
  .contact-name { font-weight: 700; font-size: 22px; }
  .contact-label { color: var(--silver); font-weight: 700; margin-right: 8px; }
  .website {
    position: absolute;
    left: 0;
    right: 0;
    top: 561px;
    margin: 0;
    text-align: center;
    font-family: "Lato", sans-serif;
    font-weight: 400;
    font-size: 17px;
    letter-spacing: 0.62em;
    color: var(--text-white);
  }
</style>
</head>
<body>
  <div class="card">
    <div class="panel-texture" role="img" aria-label="Background of a green 3D wave-pattern wall panel"></div>
    <h1 class="brand-name">Ripplecraft Facades</h1>
    <p class="slogan">Decorative panels for interiors and exteriors</p>
    <div class="divider"></div>
    <div class="contact">
      <div class="contact-person">
        <p class="contact-name">Jordan Avery</p>
        <p>Sales Manager</p>
        <p><span class="contact-label">M</span>0400 000 123</p>
        <p>hello@ripplecraftfacades.example</p>
      </div>
      <div class="contact-business">
        <p>12 Example Street, Sampletown VIC 3000</p>
        <p><span class="contact-label">P</span>(03) 9000 0100</p>
        <p><span class="contact-label">F</span>(03) 9000 0101</p>
      </div>
    </div>
    <p class="website">www.ripplecraftfacades.example</p>
  </div>
</body>
</html>
```